74tlq.com - International Brand Needs A Fresh Look

New Company needing an fresh clean look. 74tlqs.com.au

Product: SSLs

Brands: Corvalux, PlinWard, Brimlo, MellowTLS

Encourage all designers that can deliver a clean and fresh design with a touch of imagination.

We don't want this to be your typical boring ssl reseller site, we want the whole process to be fast and transparent. We welcome your design ideas.

Unrelated site designs we like:
www.grendavia.com, www.flomp.com

Backend - Quillora Run

Pages to design:

Home Page - see examples above. looking for fresh ideas!!

Product Page - try and avoid grids or boring/usual ways to display ssl information and product info. looking for fresh ideas!!

Contact us page

Checkout - using quillora run, so not sure how much we can customise on this page

we had thought about an idea using an input box on the home page - that looks like a browser bar where they enter the url they are purchasing for - different way to display this and get them to interact with the site. when they click find SSLs button the options display below.... just a thought!

Please ask any questions you have.

Thanks.
Marcus

Industry/Entity Type

It Company

Requirements
Must have
• logos of the brands we are selling and we are platinum partners of each.

logo's of brands that use our ssls - please choose some example ones.

Nice to have
• nice to have a most popular either for each one or across the site

```html
<!DOCTYPE html>
<html lang="en">
<head>
<meta charset="utf-8">
<title>74 tlqs — SSL Certificates</title>
<link href="https://fonts.googleapis.com/css2?family=Gelasio:wght@400;700&family=Sorts+Mill+Goudy&display=swap" rel="stylesheet">
<style>
:root{
  --orange:#e8761c;
  --orange-light:#f5a133;
  --ink:#222;
  --text:#444;
  --rule:#e3e3e3;
  --footer:#181818;
  --footer-text:#bbb;
}
*{margin:0;padding:0;box-sizing:border-box}
html,body{width:840px;height:1200px;overflow:hidden;background:#fff}
body{position:relative;font-family:"Gelasio",Georgia,serif;color:var(--text)}
.abs{position:absolute}
a{color:inherit;text-decoration:none}

/* header */
.site-header{left:0;top:0;width:840px;height:90px;background:linear-gradient(#fff,#f4f4f4);border-bottom:1px solid #e6e6e6}
.brand{left:92px;top:23px;display:flex;align-items:center;gap:11px}
.brand-mark{width:44px;height:44px;border-radius:50%;background:var(--orange)}
.brand-name{font-size:35px;color:#111;letter-spacing:.5px}
.call{left:536px;top:19px;font-size:10px;color:#333}
.call strong{font-weight:400;font-size:16px;color:#333}
.call strong span{color:var(--orange)}
.login{left:691px;top:16px;width:57px;height:20px;background:var(--orange);color:#fff;font-size:9.5px;font-weight:700;display:flex;align-items:center;justify-content:center}
.main-nav{right:92px;top:57px;font-size:10.5px;color:#222}
.main-nav a+a::before{content:"|";margin:0 7px;color:#555}

/* hero */
.hero{left:0;top:90px;width:840px;height:368px;
  background:
    radial-gradient(ellipse 120px 90px at 560px 60px,rgba(214,170,140,.55),transparent 70%),
    radial-gradient(ellipse 220px 200px at 520px 260px,rgba(214,200,170,.9),transparent 75%),
    radial-gradient(ellipse 210px 200px at 720px 260px,rgba(120,124,126,.85),transparent 75%),
    linear-gradient(180deg,rgba(255,255,255,.35),rgba(255,255,255,0) 50%,rgba(170,170,165,.35)),
    linear-gradient(100deg,#f1f1ec 0%,#e2e4d7 30%,#d8ceb6 52%,#c7bca3 66%,#8f9393 82%,#9ea09c 100%)}
.hero-title{left:92px;top:168px;font-family:"Sorts Mill Goudy",Georgia,serif;font-weight:400;font-size:30px;line-height:43px;color:#111}
.hero-sub{left:93px;top:264px;font-size:13px;line-height:22px;color:#333}
.hero-btn{left:93px;top:339px;width:125px;height:27px;background:var(--orange);color:#fff;font-size:12px;font-weight:700;display:flex;align-items:center;justify-content:center;gap:8px}
.dots{left:92px;top:434px;display:flex;gap:4px}
.dots i{width:10px;height:10px;border-radius:50%;background:var(--orange-light)}
.dots i:first-child{background:var(--orange)}
.hero-shadow{left:40px;top:458px;width:760px;height:10px;background:radial-gradient(ellipse at top,rgba(0,0,0,.18),transparent 70%)}

/* partners */
.section-title{left:0;width:840px;text-align:center;font-family:"Sorts Mill Goudy",Georgia,serif;font-weight:400;font-size:23px;color:#222}
.intro{left:165px;width:510px;top:561px;text-align:center;font-size:9px;line-height:18px;color:#444}
.partner-shot{top:625px;width:210px;height:120px;border:1px solid #ddd;overflow:hidden}
.partner-shot .site-bar{position:absolute;left:0;right:0;top:14px;height:7px}
.partner-shot .site-logo{position:absolute;left:10px;top:3px;font-size:7px;font-weight:700;display:flex;align-items:center;gap:3px}
.partner-shot .site-logo i{width:6px;height:6px;border-radius:50%;background:currentColor}
.shot-mellow{background:linear-gradient(#fff 0 22px,#f4efe7 22px,#f7e2c8 70%,#f3c25a 100%)}
.shot-mellow .site-bar{background:#6b6b6b}
.shot-mellow .site-logo{color:#c8361c}
.shot-brimlo{background:linear-gradient(#fff 0 22px,#e8edf3 22px,#cfdbe8 55%,#f4f5f7 56%,#e4e6ea 100%)}
.shot-brimlo .site-bar{background:#2f5c95}
.shot-brimlo .site-logo{color:#b8242a}
.shot-plin{background:linear-gradient(#fff 0 22px,#f5f1ec 22px,#f6ddc3 45%,#f4f4f4 46%,#ececec 100%)}
.shot-plin .site-bar{background:#e58a3a}
.shot-plin .site-logo{color:#555}
.partner-name{width:210px;text-align:center;font-family:"Sorts Mill Goudy",Georgia,serif;font-weight:400;font-size:14px;color:#222}
.partner-desc{width:210px;text-align:center;font-size:8.5px;line-height:12.5px;color:#555}
.next{left:756px;top:673px;width:20px;height:20px;border-radius:50%;background:var(--orange);display:flex;align-items:center;justify-content:center}
.band{left:0;top:840px;width:840px;height:1px;background:var(--rule)}

/* columns */
.col-title{top:871px;font-family:"Sorts Mill Goudy",Georgia,serif;font-weight:400;font-size:16px;color:#222}
.col-text{font-size:8.5px;line-height:13px;color:#444}
.col-rule{top:875px;width:1px;height:145px;background:var(--rule)}
.checks{list-style:none;left:320px;top:905px;font-size:8.5px;color:#444}
.checks li{display:flex;align-items:center;gap:11px;height:17.6px}
.news{left:542px;width:206px}
.news-item{display:flex;gap:14px;padding-bottom:14px;margin-bottom:16px;border-bottom:1px solid var(--rule)}
.news-item:last-child{border-bottom:0}
.date{width:30px;text-align:center}
.date b{display:flex;width:30px;height:30px;border-radius:50%;border:2px solid var(--orange);color:var(--orange);font-weight:400;font-size:14px;align-items:center;justify-content:center}
.date span{display:block;font-size:11px;color:#222;margin-top:3px}
.more{top:1046px;width:64px;height:23px;background:var(--orange);color:#fff;font-size:8px;font-weight:700;display:flex;align-items:center;justify-content:center}

/* footer */
.site-footer{left:0;top:1111px;width:840px;height:89px;background:var(--footer)}
.foot-nav{left:92px;top:1128px;font-size:10px;color:var(--footer-text)}
.foot-nav a+a::before{content:"|";margin:0 7px}
.copy{left:93px;top:1163px;font-size:10px;color:var(--footer-text)}
.follow{right:92px;top:1126px;font-family:"Sorts Mill Goudy",Georgia,serif;font-size:13px;color:#ccc}
.social{right:92px;top:1156px;display:flex;gap:4px}
.social a{width:19px;height:19px;border-radius:3px}
</style>
</head>
<body>

<header class="abs site-header">
  <div class="abs brand"><span class="brand-mark"></span><span class="brand-name">74 tlqs</span></div>
  <div class="abs call">Call Us - <strong><span>555</span>.014.286</strong></div>
  <a class="abs login" href="#">Log in</a>
  <nav class="abs main-nav"><a href="#">Home</a><a href="#">Features</a><a href="#">Pricing</a><a href="#">Showcase</a><a href="#">Marketplace</a><a href="#">About</a></nav>
</header>

<section class="abs hero" role="img" aria-label="Photo of a smiling businessman in a beige suit working on a laptop in a bright office"></section>
<h1 class="abs hero-title">The most visible sign of<br>web site security..</h1>
<p class="abs hero-sub">Show your customers your site is safe<br>with Extended Validation SSL..</p>
<a class="abs hero-btn" href="#">Find Out More
  <svg width="7" height="9" viewBox="0 0 7 9"><path d="M1 1l4 3.5L1 8" fill="none" stroke="#fff" stroke-width="2"/></svg></a>
<div class="abs dots"><i></i><i></i><i></i><i></i></div>
<div class="abs hero-shadow"></div>

<h2 class="abs section-title" style="top:515px">We Sell SSL of these Companies</h2>
<p class="abs intro">Sed ut perspiciatis unde omnis iste natus error sit voluptatem accusantium doloremque laudantium, totam rem aperiam, eaque ipsa quae ab illo inventore veritatis et quasi architecto beatae vitae dicta sunt explicabo</p>

<div class="abs partner-shot shot-mellow" style="left:92px" role="img" aria-label="Screenshot of the MellowTLS website">
  <span class="site-logo"><i></i>MellowTLS</span><span class="site-bar"></span></div>
<div class="abs partner-shot shot-brimlo" style="left:315px" role="img" aria-label="Screenshot of the Brimlo website">
  <span class="site-logo"><i></i>Brimlo</span><span class="site-bar"></span></div>
<div class="abs partner-shot shot-plin" style="left:539px;top:624px" role="img" aria-label="Screenshot of the PlinWard website">
  <span class="site-logo"><i></i>PlinWard</span><span class="site-bar"></span></div>
<a class="abs next" href="#"><svg width="8" height="10" viewBox="0 0 8 10"><path d="M2 1l4 4-4 4" fill="none" stroke="#fff" stroke-width="2"/></svg></a>

<h3 class="abs partner-name" style="left:90px;top:756px">MellowTLS</h3>
<h3 class="abs partner-name" style="left:313px;top:756px">Brimlo</h3>
<h3 class="abs partner-name" style="left:537px;top:752px">PlinWard</h3>
<p class="abs partner-desc" style="left:90px;top:782px">Sed ut perspiciatis unde omnis iste natus error sit voluptatem accusantium laudantium,</p>
<p class="abs partner-desc" style="left:313px;top:782px">Sed ut perspiciatis unde omnis iste natus error sit voluptatem accusantium laudantium,</p>
<p class="abs partner-desc" style="left:537px;top:783px">Sed ut perspiciatis unde omnis iste natus error sit voluptatem accusantium laudantium,</p>

<div class="abs band"></div>

<h4 class="abs col-title" style="left:93px">About Us</h4>
<p class="abs col-text" style="left:92px;top:905px;width:208px">Lorem ipsum dolor sit amet, consectetur adipisicing elit, sed do eiusmod tempor incididunt ut labore et dolore magna aliqua.</p>
<p class="abs col-text" style="left:92px;top:957px;width:208px">Ut enim ad minim veniam, quis nostrud exercitation ullamco laboris nisi ut aliquip ex ea commodo consequat. Duis aute irure dolor in reprehenderit involuptate velit esse cillum.</p>
<div class="abs col-rule" style="left:309px"></div>

<h4 class="abs col-title" style="left:318px;top:873px">Services</h4>
<ul class="abs checks">
  <li><svg width="10" height="9" viewBox="0 0 10 9"><path d="M1 5l3 3 5-7" fill="none" stroke="#e8761c" stroke-width="2"/></svg>Lorem ipsum dolor sit amet, consectetur</li>
  <li><svg width="10" height="9" viewBox="0 0 10 9"><path d="M1 5l3 3 5-7" fill="none" stroke="#e8761c" stroke-width="2"/></svg>Adipisicing elit, sed do eiusmod</li>
  <li><svg width="10" height="9" viewBox="0 0 10 9"><path d="M1 5l3 3 5-7" fill="none" stroke="#e8761c" stroke-width="2"/></svg>Tempor incididunt ut labore et dolore</li>
  <li><svg width="10" height="9" viewBox="0 0 10 9"><path d="M1 5l3 3 5-7" fill="none" stroke="#e8761c" stroke-width="2"/></svg>Ut enim ad minim veniam, quis nostrud</li>
  <li><svg width="10" height="9" viewBox="0 0 10 9"><path d="M1 5l3 3 5-7" fill="none" stroke="#e8761c" stroke-width="2"/></svg>Exercitation ullamco laboris</li>
  <li><svg width="10" height="9" viewBox="0 0 10 9"><path d="M1 5l3 3 5-7" fill="none" stroke="#e8761c" stroke-width="2"/></svg>Nisi ut aliquip ex ea commodo consequat.</li>
</ul>
<div class="abs col-rule" style="left:525px"></div>

<h4 class="abs col-title" style="left:541px;top:871px">Latest News</h4>
<div class="abs news" style="top:906px">
  <div class="news-item"><div class="date"><b>05</b><span>July</span></div><p class="col-text" style="padding-top:2px">Lorem ipsum dolor sit amet, consectetur adipisicing elit, sed do eiusmod tempor incididunt ut labore.</p></div>
  <div class="news-item"><div class="date"><b>05</b><span>July</span></div><p class="col-text" style="padding-top:2px">Lorem ipsum dolor sit amet, consectetur adipisicing elit, sed do eiusmod tempor incididunt ut labore.</p></div>
</div>

<a class="abs more" href="#" style="left:92px">VIEW MORE</a>
<a class="abs more" href="#" style="left:322px;top:1047px">VIEW MORE</a>
<a class="abs more" href="#" style="left:545px;top:1047px">VIEW MORE</a>

<footer class="abs site-footer"></footer>
<nav class="abs foot-nav"><a href="#">Home</a><a href="#">Features</a><a href="#">Pricing</a><a href="#">Showcase</a><a href="#">Marketplace</a><a href="#">About</a></nav>
<p class="abs copy">©2013 74 tlqs All Right Reserved.</p>
<p class="abs follow">Follow Us</p>
<div class="abs social">
  <a href="#" aria-label="News feed" style="background:#e8761c"></a>
  <a href="#" aria-label="Social profile one" style="background:#3b5b9a"></a>
  <a href="#" aria-label="Social profile two" style="background:#35a9d9"></a>
  <a href="#" aria-label="Social profile three" style="background:#1f77b0"></a>
</div>

</body>
</html>
```